Velqar Australia Pty Ltd - Stationary design

We need letterheads for hard copy print and e-copy word docs, envelopes - landscape and A3, business cards, With compliment slips and a gloss presentation folder to hold up to 20 A4 pages
Would also like to know what font and size would be recommended to suit our brand.
Logo, Colours, Brand and image can be viewed on www.velqar.com.au

Target Market(s)

Those in pain from 30yrs to 80yrs

Industry/Entity Type

Landscape

Requirements
Must have
• Logo as per trademarked logo on web site
Nice to have
• same colours as our web site logo and design
Should not have
• anything looking cheap or too common
text and font needs to be easy to read but very professional in appearance

```html
<!DOCTYPE html>
<html lang="en">
<head>
<meta charset="utf-8">
<title>Velqar Australia – Stationery Options</title>
<link href="https://fonts.googleapis.com/css2?family=Source+Sans+3:wght@400;600;700&family=Open+Sans:wght@300&family=Jost:wght@400&display=swap" rel="stylesheet">
<style>
  :root{
    --stage:#262626;
    --stage-edge:#1a1a1a;
    --paper-top:#ffffff;
    --paper-bottom:#e9e9e9;
    --navy:#1b3a73;
    --sky:#3fb3e6;
    --ink:#333333;
    --ink-soft:#555555;
    --rule:#444444;
    --label:#f2f2f2;
  }
  *{box-sizing:border-box;margin:0;padding:0}
  html,body{width:1200px;height:575px;overflow:hidden}
  body{
    background:radial-gradient(ellipse at 50% 40%,var(--stage) 0%,var(--stage-edge) 100%);
    font-family:"Source Sans 3",Arial,sans-serif;
    color:var(--ink);
    position:relative;
  }
  .sheet{
    position:absolute;top:53px;width:364px;height:470px;
    background:linear-gradient(160deg,var(--paper-top) 0%,var(--paper-top) 40%,var(--paper-bottom) 100%);
    box-shadow:0 2px 8px rgba(0,0,0,.5);
    overflow:hidden;
  }
  .sheet--one{left:3px}
  .sheet--two{left:402px}
  .sheet--three{left:807px}

  .brand{
    position:absolute;top:20px;
    font-weight:700;font-size:24px;line-height:1;letter-spacing:-.3px;
    color:var(--navy);white-space:nowrap;
    display:flex;align-items:center;gap:6px;
  }
  .brand__dot{width:9px;height:9px;border-radius:50%;background:var(--navy)}
  .sheet--one .brand{left:50%;transform:translateX(-50%)}
  .sheet--two .brand,.sheet--three .brand{left:12px}

  .head-contact{
    position:absolute;top:20px;left:268px;
    font-size:6px;line-height:7.3px;color:var(--ink-soft);
    border-left:1px solid #999;padding-left:4px;
  }
  .head-contact strong{font-weight:700;color:var(--ink)}
  .sheet--three .head-contact{left:277px}

  .foot-plain{
    position:absolute;left:0;right:0;bottom:7px;text-align:center;
    font-size:6px;line-height:9px;color:var(--ink-soft);
  }
  .foot-plain strong{color:var(--ink);font-weight:700}
  .sep{display:inline-block;width:1px;height:6px;background:#888;margin:0 4px;vertical-align:-1px}

  .foot-band{
    position:absolute;left:0;right:0;bottom:0;height:17px;
    background:var(--navy);border-top:2px solid var(--sky);
    color:#fff;font-size:5.6px;line-height:15px;text-align:center;white-space:nowrap;
  }
  .foot-band strong{font-weight:700}
  .foot-band .sep{background:#c9d3e6}
  .icon{display:inline-block;width:5px;height:5px;vertical-align:-1px;margin-right:1px}

  .fax__title{
    position:absolute;left:27px;top:106px;
    font-family:"Jost",sans-serif;font-weight:400;font-size:24px;line-height:1;color:#111;letter-spacing:.5px;
  }
  .fax__row{position:absolute;left:27px;width:310px;height:10px;border-bottom:1px solid var(--rule)}
  .fax__label{position:absolute;bottom:1px;font-size:6.5px;font-weight:400;color:var(--ink)}
  .fax__label--right{left:184px}
  .fax__checks{position:absolute;left:27px;top:240px;width:310px;display:flex;justify-content:space-between}
  .check{display:flex;align-items:center;gap:4px;font-size:6.5px;font-weight:400;color:var(--ink)}
  .check__box{width:8px;height:8px;border:1px solid #333;background:#fff}

  .option-label{
    position:absolute;top:533px;width:364px;text-align:center;
    font-family:"Open Sans",sans-serif;font-weight:300;font-size:27px;color:var(--label);
  }
</style>
</head>
<body>

<section class="sheet sheet--one" aria-label="Letterhead option 1">
  <div class="brand"><span class="brand__dot"></span>Velqar Australia</div>
  <footer class="foot-plain">
    <div><strong>Velqar Australia Pty Ltd</strong><span class="sep"></span>Unit 12/40 Marlow Street, Halvern, NSW 2199, Australia</div>
    <div>
      <svg class="icon" viewBox="0 0 10 10"><path d="M2 1l2 0 1 2-1 1a5 5 0 002 2l1-1 2 1 0 2c-4 0-7-3-7-7z" fill="#555"/></svg>1300 555 018
      <svg class="icon" viewBox="0 0 10 10"><rect x="1" y="2" width="8" height="6" fill="#555"/></svg>admin@velqar.com.au
      <svg class="icon" viewBox="0 0 10 10"><circle cx="5" cy="5" r="4" fill="#555"/></svg>velqar.com.au<span class="sep"></span>ACN 123 456 789
    </div>
  </footer>
</section>

<section class="sheet sheet--two" aria-label="Letterhead option 2">
  <div class="brand"><span class="brand__dot"></span>Velqar Australia</div>
  <div class="head-contact">
    <strong>Velqar Australia Pty Ltd</strong><br>
    Unit 12/40 Marlow Street<br>
    Halvern, NSW 2199, Australia
  </div>
  <footer class="foot-band">
    <svg class="icon" viewBox="0 0 10 10"><path d="M2 1l2 0 1 2-1 1a5 5 0 002 2l1-1 2 1 0 2c-4 0-7-3-7-7z" fill="#fff"/></svg>1300 555 018&nbsp;
    <svg class="icon" viewBox="0 0 10 10"><rect x="1" y="2" width="8" height="6" fill="#fff"/></svg>admin@velqar.com.au&nbsp;
    <svg class="icon" viewBox="0 0 10 10"><circle cx="5" cy="5" r="4" fill="#fff"/></svg>velqar.com.au<span class="sep"></span>ACN 123 456 789
  </footer>
</section>

<section class="sheet sheet--three" aria-label="Fax sheet option 3">
  <div class="brand"><span class="brand__dot"></span>Velqar Australia</div>
  <div class="head-contact">
    <svg class="icon" viewBox="0 0 10 10"><path d="M2 1l2 0 1 2-1 1a5 5 0 002 2l1-1 2 1 0 2c-4 0-7-3-7-7z" fill="#555"/></svg>1300 555 018<br>
    <svg class="icon" viewBox="0 0 10 10"><rect x="1" y="2" width="8" height="6" fill="#555"/></svg>admin@velqar.com.au<br>
    <svg class="icon" viewBox="0 0 10 10"><circle cx="5" cy="5" r="4" fill="#555"/></svg>velqar.com.au
  </div>

  <div class="fax__title">FAX</div>
  <div class="fax__row" style="top:151px"><span class="fax__label">To :</span><span class="fax__label fax__label--right">From :</span></div>
  <div class="fax__row" style="top:170px"><span class="fax__label">Fax :</span><span class="fax__label fax__label--right">Pages :</span></div>
  <div class="fax__row" style="top:189px"><span class="fax__label">Phone :</span><span class="fax__label fax__label--right">Date :</span></div>
  <div class="fax__row" style="top:209px"><span class="fax__label">Re :</span><span class="fax__label fax__label--right">CC :</span></div>

  <div class="fax__checks">
    <span class="check"><span class="check__box"></span>Urgent</span>
    <span class="check"><span class="check__box"></span>For Review</span>
    <span class="check"><span class="check__box"></span>Please Comment</span>
    <span class="check"><span class="check__box"></span>Please Reply</span>
    <span class="check"><span class="check__box"></span>Please Recycle</span>
  </div>

  <footer class="foot-band">
    <strong>Velqar Australia Pty Ltd</strong><span class="sep"></span>Unit 12/40 Marlow Street, Halvern, NSW 2199, Australia
  </footer>
</section>

<div class="option-label" style="left:3px">Option-1</div>
<div class="option-label" style="left:402px">Option-2</div>
<div class="option-label" style="left:807px">Option-3</div>

</body>
</html>
```